Flyer für Immobilienmaklerunternehmen
Zielgruppe
Wir sind ein Immobilienmaklerunternehmen in Bochum.
Wir lassen die Flyer in die Briefkästen verteilen.
Wir möchten Eigentümer erreichen und diese am Besten zur Kontaktaufnahme motivieren. Oder zumindest in Erinnerung bleiben.
Viele brauchen unsere Dienstleistungen nur zu einem bestimmten Zeitpunkt.
Unsere Zielgruppe sind meist ältere Eigentümer, die entweder aus Sorge, wegen privatem Stress, Unwissenheit oder Erlösmaximierung einen Makler beauftragen.
Wir würden gerne mit den Flyern diejenigen ansprechen, die Sorge haben und ggf. unwissend sind. Hierbei stellen wir uns einen Flyer vor, der auf der Vorderseite ein Bild mit 'unsicheren Zeiten' nutzt, um Aufmerksamkeit zu erregen (wir haben bspw. einen Flyer mit einem Leuchtturm gesehen, der durch den Sturm den Weg weist, mit dem Spruch' Wir geben Ihnen auch in stürmischen Zeiten eine sichere Orientierung' etwas Ähnliches stellen wir uns vor) mit einem passenden Slogan.
Zudem hätten wir auf der Vorderseite ebenso unser Logo, als auch das Zertifikat.
Auf der Rückseite gerne die Motivation zur Kontaktaufnahme wie oben beschrieben, zudem hatten wir uns eine kurze Vorstellung unserer Dienstleistungen (Verkauf, Wertgutachten, Vermietung, Wohnflächenberechnung und Energieausweis) vorgestellt.
Dann hätten wir entweder gerne ein Teamfoto eingebaut mit Einladung zur Kontaktaufnahme, alternativ unseren Slogan 'Unser Erstgespräch kostet Sie einen Kaffee und einen Keks.' und anstelle des Teamfotos dann einem Bild von Kaffee und Keksen o.Ä.
Die Adressdaten der Firmen bitte sehr dezent/klein plazieren.
Bitte diese beiden Büros einbauen:
Kessling Immobilien
Wendelgasse 417
44879 Bochum
www.kessling-immobilien-beispiel.info
und
Tubel Immobilien
Lindmarkweg 27
44649 Herne
www.tubel-beispiel.de
(Bitte die Logos von der Homepage verwenden)
Aufgabenstellung
Unser Logo sollte zu finden sein, sowie die Geschäftsfarben (aus dem Logo)
Zudem muss die Handhabbarkeit beim Verteilen gegeben sein.
Wir kennen uns nicht so gut aus und benötigen am Schluss ein Ergebnis, mit dem wir die Flyer direkt drucken lassen können.
Bei Spezialformaten freuen wir uns, wenn Sie uns sagen, wo man diese drucken lassen kann.

```html
<!DOCTYPE html>
<html lang="de">
<head>
<meta charset="utf-8">
<title>Flyer Kessling Immobilien</title>
<link rel="stylesheet" href="https://fonts.googleapis.com/css2?family=Alfa+Slab+One&family=Jost:wght@400;500;600&family=Oswald:wght@400;500&display=swap">
<style>
  :root {
    --brand-green: #7cbf2a;
    --ink: #1f1f1f;
    --paper: #ffffff;
    --canvas: #ffffff;
    --soft-grey: #f2f3f3;
    --badge-navy: #23407a;
    --forest-dark: #2b301f;
    --forest-mid: #6d7443;
    --forest-light: #d8cd92;
  }
  * { margin: 0; padding: 0; box-sizing: border-box; }
  html, body { width: 1200px; height: 1200px; overflow: hidden; background: var(--canvas); }
  body { position: relative; font-family: "Jost", sans-serif; color: var(--ink); }

  .flyer { position: absolute; width: 470px; background: var(--paper); overflow: hidden; }
  .flyer--front { left: 112px; top: 119px; height: 934px; }
  .flyer--back { left: 650px; top: 111px; height: 941px; }

  .brand {
    position: absolute; background: var(--paper);
    display: flex; flex-direction: column; align-items: center; justify-content: center; gap: 7px;
  }
  .brand__square { width: 12px; height: 12px; background: var(--brand-green); flex: none; }
  .brand__name {
    font-family: "Jost", sans-serif; font-weight: 500; font-size: 14px;
    letter-spacing: 1.5px; text-transform: uppercase; color: var(--ink);
    line-height: 1.3; text-align: center;
  }

  /* front */
  .front__photo {
    position: absolute; left: 0; top: 82px; width: 470px; height: 796px;
    background:
      radial-gradient(ellipse 170px 300px at 110px 300px, rgba(255,240,185,0.9), rgba(255,240,185,0) 75%),
      radial-gradient(ellipse 260px 220px at 240px 380px, rgba(226,214,150,0.55), rgba(226,214,150,0) 80%),
      linear-gradient(90deg, rgba(40,45,28,0.55) 0%, rgba(40,45,28,0) 22%, rgba(40,45,28,0) 70%, rgba(40,45,28,0.6) 100%),
      linear-gradient(180deg, #4f5a30 0%, #8c8e55 22%, var(--forest-light) 42%, #9ea065 58%, var(--forest-mid) 70%, #3f4829 84%, var(--forest-dark) 100%);
  }
  .front__brand { left: 24px; top: 21px; width: 137px; height: 108px; }
  .front__headline {
    position: absolute; right: 28px; top: 24px; text-align: right;
    font-family: "Alfa Slab One", serif; font-weight: 400; color: var(--brand-green);
    font-size: 56px; line-height: 59px;
  }
  .certificate {
    position: absolute; left: 264px; top: 683px; width: 173px; height: 78px;
    background: rgba(205,210,210,0.92); display: flex; align-items: center; gap: 7px; padding: 0 6px;
  }
  .certificate__seal { width: 64px; height: 64px; border-radius: 50%; background: var(--paper); border: 4px solid var(--badge-navy); flex: none; }
  .certificate__text { font-family: "Oswald", sans-serif; font-size: 9.5px; line-height: 13.5px; color: var(--paper); }
  .front__slogan {
    position: absolute; left: 25px; top: 775px;
    font-family: "Alfa Slab One", serif; font-weight: 400; color: var(--brand-green);
    font-size: 38.5px; line-height: 41px; letter-spacing: -0.3px; white-space: nowrap;
  }
  .band {
    position: absolute; left: 0; bottom: 0; width: 100%;
    background: var(--brand-green); color: var(--paper);
    display: flex; align-items: center; justify-content: center; white-space: nowrap;
  }
  .front__band { height: 56px; font-size: 22px; }

  /* back */
  .back__brand { left: 292px; top: 29px; width: 129px; height: 108px; }
  .services__title {
    position: absolute; left: 50px; top: 80px;
    font-weight: 600; font-size: 27px; line-height: 34px; color: var(--brand-green);
  }
  .services__list { position: absolute; left: 50px; top: 157px; list-style: none; }
  .services__item { display: flex; align-items: center; height: 37.7px; font-size: 23px; }
  .services__tick { width: 20px; height: 20px; margin-right: 27px; flex: none; }
  .callout {
    position: absolute; left: 50px; top: 422px; width: 375px;
    display: flex; align-items: center; justify-content: space-between;
  }
  .callout__arrow { width: 24px; height: 38px; flex: none; }
  .callout__text {
    font-family: "Oswald", sans-serif; font-weight: 400; color: var(--brand-green);
    font-size: 23.5px; line-height: 33px; white-space: nowrap;
  }
  .back__lower { position: absolute; left: 0; top: 551px; width: 100%; height: 334px; background: var(--soft-grey); }
  .back__photo {
    position: absolute; left: 0; top: 0; width: 100%; height: 212px;
    background:
      radial-gradient(ellipse 110px 90px at 230px 150px, rgba(214,102,142,0.45), rgba(214,102,142,0) 80%),
      radial-gradient(ellipse 120px 110px at 230px 60px, rgba(80,130,50,0.35), rgba(80,130,50,0) 80%),
      linear-gradient(90deg, #eceeed 0%, #b9a99a 18%, #e7e3df 32%, #e7e3df 58%, #5b5b5b 76%, #2e2e2e 100%);
  }
  .contacts { position: absolute; left: 56px; top: 221px; width: 380px; display: flex; font-size: 12px; line-height: 15px; }
  .contacts__office { width: 188px; font-style: normal; }
  .contacts__office--second { padding-left: 43px; border-left: 1px solid #555; }
  .contacts__phone { font-weight: 600; font-size: 13px; }
  .contacts__web { font-size: 11px; }
  .back__band { height: 56px; font-size: 14.5px; letter-spacing: -0.2px; }
</style>
</head>
<body>

<section class="flyer flyer--front">
  <div class="front__photo" role="img" aria-label="Lichtdurchfluteter Wald mit hohen Bäumen im Morgennebel"></div>
  <div class="brand front__brand">
    <span class="brand__square"></span>
    <span class="brand__name">Kessling<br>Immobilien</span>
  </div>
  <h1 class="front__headline">Lauter<br>Bäume?</h1>
  <div class="certificate">
    <span class="certificate__seal" role="img" aria-label="Zertifikatssiegel"></span>
    <p class="certificate__text">Unser Unternehmen<br>erfüllt die Vorschriften<br>der DIN EN 15733<br>seit 2017</p>
  </div>
  <p class="front__slogan">Wir helfen Ihnen<br>den Wald zu sehen.</p>
  <div class="band front__band">Ihr Immobilienmarkler aus Bochum.</div>
</section>

<section class="flyer flyer--back">
  <div class="brand back__brand">
    <span class="brand__square"></span>
    <span class="brand__name">Kessling<br>Immobilien</span>
  </div>
  <h2 class="services__title">Unsere<br>Dienstleistungen:</h2>
  <ul class="services__list">
    <li class="services__item"><svg class="services__tick" viewBox="0 0 20 20"><rect x="1" y="3" width="16" height="16" fill="none" stroke="var(--brand-green)" stroke-width="2"/><path d="M4 10 L8 15 L18 1" fill="none" stroke="var(--brand-green)" stroke-width="2.2"/></svg>Verkauf</li>
    <li class="services__item"><svg class="services__tick" viewBox="0 0 20 20"><rect x="1" y="3" width="16" height="16" fill="none" stroke="var(--brand-green)" stroke-width="2"/><path d="M4 10 L8 15 L18 1" fill="none" stroke="var(--brand-green)" stroke-width="2.2"/></svg>Wertgutachten</li>
    <li class="services__item"><svg class="services__tick" viewBox="0 0 20 20"><rect x="1" y="3" width="16" height="16" fill="none" stroke="var(--brand-green)" stroke-width="2"/><path d="M4 10 L8 15 L18 1" fill="none" stroke="var(--brand-green)" stroke-width="2.2"/></svg>Vermietung</li>
    <li class="services__item"><svg class="services__tick" viewBox="0 0 20 20"><rect x="1" y="3" width="16" height="16" fill="none" stroke="var(--brand-green)" stroke-width="2"/><path d="M4 10 L8 15 L18 1" fill="none" stroke="var(--brand-green)" stroke-width="2.2"/></svg>Wohnflächenberechnung</li>
    <li class="services__item"><svg class="services__tick" viewBox="0 0 20 20"><rect x="1" y="3" width="16" height="16" fill="none" stroke="var(--brand-green)" stroke-width="2"/><path d="M4 10 L8 15 L18 1" fill="none" stroke="var(--brand-green)" stroke-width="2.2"/></svg>Energieausweis</li>
  </ul>
  <div class="callout">
    <svg class="callout__arrow" viewBox="0 0 24 38"><path d="M3 3 L20 19 L3 35" fill="none" stroke="var(--brand-green)" stroke-width="6"/></svg>
    <p class="callout__text">Rufen Sie uns an und vereinbaren<br>ein unverbindliches Erstgespräch.</p>
    <svg class="callout__arrow" viewBox="0 0 24 38"><path d="M21 3 L4 19 L21 35" fill="none" stroke="var(--brand-green)" stroke-width="6"/></svg>
  </div>
  <div class="back__lower">
    <div class="back__photo" role="img" aria-label="Tasse Cappuccino, Strauß rosa Rosen, schwarzes Notizbuch und Donut auf hellem Tisch"></div>
    <div class="contacts">
      <address class="contacts__office">
        Kessling Immobilien<br>Wendelgasse 417<br>44879 Bochum<br>
        <span class="contacts__phone">0234 / 55501234</span><br>
        <span class="contacts__web">www.kessling-immobilien-beispiel.info</span>
      </address>
      <address class="contacts__office contacts__office--second">
        Tubel Immobilien<br>Lindmarkweg 27<br>44649 Herne<br>02325/ 55508<br>
        <span class="contacts__web">www.tubel-beispiel.de</span>
      </address>
    </div>
  </div>
  <div class="band back__band">Unser Erstgespräch kostet Sie nur einen Kaffee und leckere Kekse</div>
</section>

</body>
</html>
```